Hurricane Damage Public Adjuster Billboard

I have created several projects with you and have several great designs. I need to format them into a Billboard for upcoming Hurricane Season. Need done in a month. Im also in process of getting an eye catching and easy to remember 800# Vanity phone number like Call 800-Stormsafe or 800- Need Fix? My included past Craft Huddle projects will give you an idea of what colors, schemes, and designs I gravitate towards. 3 past Design projects were 1) 2 Logos where I picked the 1st place and the 2nd place and 2) Index Card where I picked the winner as the Index Card and the 2nd place as a Post Card. Point is, I will pick and pay for 2 winners if they're good. This should help to sweeten the pot. Also, please look at my website for ideas that I like:

www.TheClaimKeeperGroup.com
I want people to feel that I am the best and highest. Level.

I've been getting a lot of quick half effort designs basically cut & pasting my previous projects. Please don't rush and take your time to be creative. A an example, my Biggest Competitor is Vesta Public Adjusting. Their colors are Black and Gold while mine are Blue, White, and Black with a highlight of Orange if possible. I JUST imported a picture of their BillBoard. I need mine better and BLOW AWAY THEIRS. Terms like "Don't be Victimized Twice ?, Don't let the Hurricane Ruin your Life?". "Get Fairly Paid & Move On" "Our Clients Claims are VIP?
Updates

I'm getting a lot of quick half effort ones. I'd rather you take your time and really put some thoughts and effort into it. My Biggest Competitor is Vesta Public Adjusting. They have black & gold colors, while I have Blue, Black, and white.

It needs to blow theirs away. I have imported their Billboard for comparative purposes.

Guy's,
I'll make it easier for you in what I'm looking for. Please look at the Vesta Billboard picture attached.

1) Put my "Blue Shield" to the left, replacing their logo
2) change color patterns from their (Black, Gold, White) to my color schemes of (Black, Blue, White)
3) I want to see my name where their is:

THE
Claim Keeper's Group
EXPERT & LOCAL Public Adjusters
"FOR THE POLICYHOLDER!!"

4) to the right, add the A+Rated logo and QRS+ Accredited logo, 5 Star Zorbix Rated logo, 5 Start PORCHLINE Highly Rated logo, etc..

5) the right side is where you can be creative as I will not have a picture of me there.

"20+ Years of Experience, Recovering Millions for our VIP Clients"

"Your Best, Locally-Based Private Adjuster & Advocate'
"FOR THE POLICYHOLDER!!"

"Don't be victimized Twice!!"

"Don't let the Hurricane Ruin Your Life!!"

This should really help. Also, refer to my website, maybe a couple testimonial fillers?

Thanks all,

marcus@TheClaimKeeperGroup.com

Just imported a few awards that would look great to the right side with all the other 5 Star Ratings and accolades.
This right section could be titled like zmy Website:

5 Star Reviews, Ratings & Awards:
4-5 Logos underneath?

Target Market(s)

Coastal place where a Hurricane 🌀 🌀 Hits

Industry/Entity Type

Hurricane Public Insurance Adjuster

Font styles to use
Sans Serif
Other font styles liked:
• Zurich fonts

Colors
0054AA
0677BA
7BADD7
CADEEF
E8F1F8
EE7325
F08F49
F5BC92
FAE3D3
FDF4ED

Requirements
Must have
• Use my past project logos, colors, and schemes to create eye grabbing BillBoard
Nice to have
Should not have
• Not be too busy, must be Easy to Read, Eye Catchy

```html
<!DOCTYPE html>
<html lang="en">
<head>
<meta charset="utf-8">
<title>Storm Damage Alert Billboard</title>
<link rel="stylesheet" href="https://fonts.googleapis.com/css2?family=Oswald:wght@500;700&family=Montserrat:wght@400;600;800&family=Ubuntu:wght@700&family=Open+Sans:ital,wght@0,400;1,400&display=swap">
<style>
  :root {
    --ink: #000000;
    --brand-blue: #0a8fe0;
    --phone-blue: #0677ba;
    --storm-red: #ee1c25;
    --orange: #f7900a;
    --teal: #0b3a52;
    --white: #ffffff;
    --page: #e9ecef;
    --storm-deep: #1b1f5c;
    --storm-mid: #4a4fa8;
    --storm-light: #b9b6ef;
  }
  * { margin: 0; padding: 0; box-sizing: border-box; }
  html, body { width: 1064px; height: 1200px; overflow: hidden; background: var(--page); }
  .billboard {
    position: absolute; left: 32px; top: 391px;
    width: 1000px; height: 417px;
    background: var(--ink); overflow: hidden;
    box-shadow: 0 8px 18px rgba(0,0,0,.35);
  }
  .storm-photo {
    position: absolute; left: 500px; top: 0; width: 500px; height: 303px;
    background:
      radial-gradient(ellipse 40% 55% at 62% 32%, rgba(185,182,239,.8), transparent 70%),
      radial-gradient(ellipse 70% 80% at 70% 40%, var(--storm-mid), transparent 75%),
      linear-gradient(90deg, var(--ink) 0%, var(--storm-deep) 35%, var(--storm-deep) 100%);
  }
  .storm-photo::after {
    content: ""; position: absolute; inset: 0;
    background: linear-gradient(180deg, transparent 50%, rgba(0,0,0,.8) 100%);
  }
  .brand-mark {
    position: absolute; left: 46px; top: 26px; width: 108px; height: 108px;
    background: var(--brand-blue); border-radius: 10px;
  }
  .brand-name {
    position: absolute; left: 180px; top: 30px; width: 315px;
    font: 400 28px/1.25 "Open Sans", sans-serif; color: var(--brand-blue);
    text-align: center; letter-spacing: .5px;
  }
  .brand-tagline {
    position: absolute; left: 180px; top: 105px; width: 315px;
    font: 400 15px/1.45 "Open Sans", sans-serif; color: var(--white); text-align: center;
  }
  .brand-tagline em { font-style: italic; display: block; }
  .rating-badge {
    position: absolute; left: 823px; top: 40px; width: 156px; height: 79px;
    border: 1px solid rgba(255,255,255,.75); border-radius: 4px;
    background: rgba(40,40,110,.35);
  }
  .headline-storm {
    position: absolute; left: 44px; top: 176px;
    font: 700 105px/1 "Oswald", sans-serif; color: var(--storm-red);
    transform: scaleX(.87); transform-origin: left top; letter-spacing: 1px;
    white-space: nowrap;
  }
  .headline-alert {
    position: absolute; left: 323px; top: 180px;
    font: 800 50px/1.04 "Montserrat", sans-serif; color: var(--white);
  }
  .claim-list {
    position: absolute; top: 186px; list-style: none;
    font: 600 11.5px/1 "Montserrat", sans-serif; color: var(--white);
  }
  .claim-list li { display: flex; align-items: center; gap: 8px; height: 23.5px; white-space: nowrap; }
  .claim-list svg { width: 10px; height: 10px; flex: none; }
  .claim-list.col-a { left: 579px; }
  .claim-list.col-b { left: 779px; }
  .bottom-band { position: absolute; left: 0; top: 303px; width: 1000px; height: 114px; background: var(--white); }
  .bottom-band svg.shapes { position: absolute; inset: 0; }
  .services-line {
    position: absolute; left: 440px; top: 0; width: 560px; height: 49px;
    display: flex; align-items: center; justify-content: center;
    font: 500 16px/1 "Oswald", sans-serif; color: var(--white);
    text-transform: uppercase; white-space: nowrap;
  }
  .services-line span { display: inline-block; transform: scaleX(.84); }
  .web-address {
    position: absolute; left: 490px; top: 49px; width: 470px; height: 65px;
    display: flex; align-items: center; justify-content: center;
    font: 400 22px/1 "Montserrat", sans-serif; color: var(--white);
  }
  .web-address b { font-weight: 800; }
  .phone-lines { position: absolute; left: 42px; top: 16px; font: 700 31px/1 "Ubuntu", sans-serif; white-space: nowrap; }
  .phone-line { display: flex; align-items: center; gap: 14px; height: 41px; }
  .phone-line svg { width: 26px; height: 26px; flex: none; }
  .call { color: var(--storm-red); }
  .number { color: var(--phone-blue); }
  .or { color: var(--ink); }
  .fix { color: var(--orange); }
</style>
</head>
<body>
<div class="billboard">
  <div class="storm-photo" role="img" aria-label="Night sky with purple storm clouds and lightning over a dark skyline"></div>

  <div class="brand-mark"></div>
  <div class="brand-name">THE CLAIM KEEPER'S GROUP</div>
  <div class="brand-tagline">INSURANCE CLAIM EXPERTS<em>FOR THE POLICYHOLDER!!</em></div>

  <div class="rating-badge"></div>

  <div class="headline-storm">STORM</div>
  <div class="headline-alert">DAMAGE<br>ALERT!</div>

  <ul class="claim-list col-a">
    <li><svg viewBox="0 0 10 10"><circle cx="5" cy="5" r="5" fill="#f7900a"/><path d="M2.6 5.2l1.7 1.6 3.2-3.4" fill="none" stroke="#fff" stroke-width="1.3"/></svg>Hurricane Damage Claims</li>
    <li><svg viewBox="0 0 10 10"><circle cx="5" cy="5" r="5" fill="#f7900a"/><path d="M2.6 5.2l1.7 1.6 3.2-3.4" fill="none" stroke="#fff" stroke-width="1.3"/></svg>Water Damage Claims</li>
    <li><svg viewBox="0 0 10 10"><circle cx="5" cy="5" r="5" fill="#f7900a"/><path d="M2.6 5.2l1.7 1.6 3.2-3.4" fill="none" stroke="#fff" stroke-width="1.3"/></svg>Wind Damage Claims</li>
    <li><svg viewBox="0 0 10 10"><circle cx="5" cy="5" r="5" fill="#f7900a"/><path d="M2.6 5.2l1.7 1.6 3.2-3.4" fill="none" stroke="#fff" stroke-width="1.3"/></svg>Roof Damage Claims</li>
  </ul>
  <ul class="claim-list col-b">
    <li><svg viewBox="0 0 10 10"><circle cx="5" cy="5" r="5" fill="#f7900a"/><path d="M2.6 5.2l1.7 1.6 3.2-3.4" fill="none" stroke="#fff" stroke-width="1.3"/></svg>Flood Damage Claims</li>
    <li><svg viewBox="0 0 10 10"><circle cx="5" cy="5" r="5" fill="#f7900a"/><path d="M2.6 5.2l1.7 1.6 3.2-3.4" fill="none" stroke="#fff" stroke-width="1.3"/></svg>Fire Damage Claims</li>
    <li><svg viewBox="0 0 10 10"><circle cx="5" cy="5" r="5" fill="#f7900a"/><path d="M2.6 5.2l1.7 1.6 3.2-3.4" fill="none" stroke="#fff" stroke-width="1.3"/></svg>Mold Growth/Damage Claims</li>
    <li><svg viewBox="0 0 10 10"><circle cx="5" cy="5" r="5" fill="#f7900a"/><path d="M2.6 5.2l1.7 1.6 3.2-3.4" fill="none" stroke="#fff" stroke-width="1.3"/></svg>Hail Damage Claims</li>
  </ul>

  <div class="bottom-band">
    <svg class="shapes" viewBox="0 0 1000 114" preserveAspectRatio="none">
      <polygon points="410,0 1000,0 1000,49 455,49" fill="#f7900a"/>
      <polygon points="455,49 1000,49 1000,114 489,114" fill="#0b3a52"/>
      <polygon points="962,49 1000,49 1000,114" fill="#ee1c25"/>
    </svg>
    <div class="services-line"><span>Expert public adjusters, loss consultants and certified insurance appraisers</span></div>
    <div class="web-address">www.<b>theclaimkeepergroup</b>.com</div>
    <div class="phone-lines">
      <div class="phone-line">
        <svg viewBox="0 0 24 24"><path d="M6.5 2.5l3 3.5-2 2.5c1.2 2.8 3.2 4.8 6 6l2.5-2 3.5 3-2 3.5C10 18.5 5.5 14 3 6.5z" fill="#0b3a52"/><path d="M14 3a7 7 0 0 1 7 7M14 6.5a3.5 3.5 0 0 1 3.5 3.5" fill="none" stroke="#0b3a52" stroke-width="1.6"/></svg>
        <span><span class="call">Call</span> <span class="number">800-Stormsafe</span></span>
      </div>
      <div class="phone-line">
        <svg viewBox="0 0 24 24"><path d="M6.5 2.5l3 3.5-2 2.5c1.2 2.8 3.2 4.8 6 6l2.5-2 3.5 3-2 3.5C10 18.5 5.5 14 3 6.5z" fill="#0b3a52"/><path d="M14 3a7 7 0 0 1 7 7M14 6.5a3.5 3.5 0 0 1 3.5 3.5" fill="none" stroke="#0b3a52" stroke-width="1.6"/></svg>
        <span><span class="or">or</span> <span class="number">800-</span> <span class="fix">Need Fix?</span></span>
      </div>
    </div>
  </div>
</div>
</body>
</html>
```